Calder Vane LED - E- Commerce site

We need a website designed for an LED Billboard company that sells:
1) LED Billboards (Sales & Rental)
2) LED Gas Station lights
3) Truss Systems (Sales & Rental)
4) Sound Systems (Sales & Rental)

Attached are websites that sell similar products as Calder Vane LED. Target market is for business, property managers and event coordinators.
This site will need to be an e-commerce site where customers can purchase the product directly from the site. What I'm looking for is a design layout to start.

Conceptual Web Designs:
http://192.0.2.47:8087/index.html
http://www.pmvdisplay.example/
http://www.auralomaaudio.example/
http://www.quillmarkpanel.example/

Attached is the logo of the company: Please note that the new spelling of the logo is "Calder Vane LED" using domain " CalderVaneLED.com

Industry/Entity Type

Gas Station

Number of Pages Required

5+ page

Requirements
Must have
• 1) E-Commerce - Customers will need to be able to order product from the site.
• 2) Customers will also have the option to rent the product as well.
Nice to have
• I like the image of the attached website, that has a video clip loop
• http://www.quillmarkpanel.example/

```html
<!DOCTYPE html>
<html lang="en">
<head>
<meta charset="utf-8">
<title>Calder Vane LED</title>
<link href="https://fonts.googleapis.com/css2?family=Arimo:wght@400;700&display=swap" rel="stylesheet">
<style>
  :root{
    --ink:#1b1b1b;
    --text:#555;
    --muted:#8a8a8a;
    --line:#dcdcdc;
    --accent-orange:#f0a21a;
    --accent-red:#d62f2b;
    --accent-blue:#163f8c;
    --accent-green:#3aa53a;
    --accent-pink:#d4286d;
    --call:#d43c6c;
    --cart:#3aaa4a;
    --band:#f3f3f3;
    --foot:#e9e9e9;
  }
  *{box-sizing:border-box;margin:0;padding:0}
  html,body{width:733px;height:1200px;overflow:hidden;background:#fff}
  body{font-family:"Arimo",Arial,sans-serif;color:var(--text);position:relative}
  .abs{position:absolute}

  .topbar{left:0;top:0;width:733px;height:78px;background:var(--ink)}
  .brand{left:82px;top:14px;display:flex;align-items:center;gap:6px;color:var(--accent-orange);font-weight:700;font-size:15px;line-height:1.05;width:110px}
  .brand .mark{width:14px;height:14px;border-radius:50%;background:var(--accent-orange);flex:none}
  .search{left:373px;top:15px;width:126px;height:21px;border:1px solid #555;border-radius:2px;color:#888;font-size:6.5px;padding:6px 8px}
  .search svg{position:absolute;right:7px;top:5px}
  .contact{top:17px;text-align:right;color:#fff;font-size:5.5px;line-height:1.4;font-weight:400}
  .contact b{display:block;font-size:7.5px;font-weight:400}
  .round{width:22px;height:22px;border-radius:50%;top:15px;display:flex;align-items:center;justify-content:center}
  .nav{top:54px;right:82px;display:flex;gap:16px;font-size:7.2px;font-weight:400;color:#cfcfcf;white-space:nowrap}
  .nav .on{color:var(--accent-orange)}

  .hero{left:0;top:78px;width:733px;height:248px;background:linear-gradient(180deg,#1c2a44 0%,#2c3a55 40%,#6d747c 75%,#8d8e8e 100%)}
  .dots{left:342px;top:303px;width:48px;height:11px;border-radius:6px;background:#3a3a3a;display:flex;gap:5px;align-items:center;justify-content:center}
  .dots i{width:4px;height:4px;border-radius:50%;background:#ddd;display:block}

  .section-title{left:80px;font-size:15px;font-weight:400}
  .pager{left:627px;display:flex;gap:1px}
  .pager span{width:12px;height:12px;border-radius:50%;border:1px solid #bbb;display:flex;align-items:center;justify-content:center}
  .card{width:135px;height:127px;border:1px solid var(--line);background:#fff}
  .card .shot{position:absolute;left:4px;top:4px;width:127px;height:89px}
  .card .caption{position:absolute;left:0;top:105px;width:100%;text-align:center;font-size:6.8px;color:#555}
  .overlay{position:absolute;left:4px;top:4px;width:127px;height:89px;background:rgba(20,20,20,.92);color:#fff;text-align:center;padding:18px 10px 0}
  .overlay h4{font-size:6.8px;font-weight:400;margin-bottom:6px}
  .overlay p{font-size:5.2px;color:#bbb;line-height:1.5}
  .overlay .price{font-size:7px;color:#fff;margin-top:10px}
  .actions{position:absolute;left:0;top:101px;width:100%;display:flex;justify-content:center;align-items:center;gap:14px}

  .about{left:0;top:938px;width:733px;height:110px;background:var(--band)}
  .about h2{position:absolute;left:81px;top:18px;font-size:15px;font-weight:400;color:var(--accent-pink)}
  .about p{position:absolute;left:81px;top:42px;width:571px;font-size:6.2px;line-height:12.8px;color:var(--muted);text-align:justify}

  .footer{left:0;top:1048px;width:733px;height:113px;background:var(--foot)}
  .fcol{top:18px;font-size:7px;color:#333}
  .fcol ul{list-style:none;margin-top:7px}
  .fcol li{font-size:6.2px;color:#777;line-height:12.8px}
  .fcol li::before{content:"•";margin-right:4px;color:#999}
  .vline{top:16px;width:1px;height:84px;background:#cfcfcf}

  .bottom{left:0;top:1161px;width:733px;height:39px;background:var(--ink)}
  .copy{left:81px;top:16px;font-size:6.2px;color:#bbb}
  .pay{top:15px;width:15px;height:9px;border-radius:1px}
  .social{top:11px;width:16px;height:16px;border-radius:50%}
</style>
</head>
<body>

<header class="abs topbar">
  <div class="abs brand"><span class="mark"></span><span>Calder Vane LED</span></div>
  <div class="abs search">Search
    <svg width="9" height="9" viewBox="0 0 10 10"><circle cx="4" cy="4" r="3" fill="none" stroke="#f0731a" stroke-width="1.4"/><line x1="6.3" y1="6.3" x2="9" y2="9" stroke="#f0731a" stroke-width="1.6"/></svg>
  </div>
  <div class="abs contact" style="right:172px">Call us on<b>555 010 4827</b></div>
  <div class="abs round" style="left:565px;background:var(--call)">
    <svg width="9" height="9" viewBox="0 0 10 10"><path d="M2 1l2 2-1 1.2c.6 1.2 1.4 2 2.6 2.6L6.8 5.8l2 2-1.3 1.3C4.5 9 1 5.5.8 2.4z" fill="#fff"/></svg>
  </div>
  <div class="abs contact" style="right:108px">My Cart<b>$00.00</b></div>
  <div class="abs round" style="left:629px;background:var(--cart)">
    <svg width="9" height="9" viewBox="0 0 10 10"><path d="M0 1h2l1.5 5h5L10 2.5H3" fill="none" stroke="#fff" stroke-width="1.2"/><circle cx="4" cy="8.5" r="1" fill="#fff"/><circle cx="8" cy="8.5" r="1" fill="#fff"/></svg>
  </div>
  <nav class="abs nav">
    <span class="on">Home</span><span>LED Billboards</span><span>Trusses</span><span>Gas Station lights</span><span>Sound Systems</span><span>About us</span><span>Contact us</span>
  </nav>
</header>

<section class="abs hero" role="img" aria-label="Night photo of a lit gas station forecourt with green canopy, pumps and parked cars"></section>
<div class="abs dots"><i></i><i></i><i></i><i></i></div>

<!-- LED Billboards -->
<h2 class="abs section-title" style="top:360px;color:var(--accent-red)">LED Billboards</h2>
<div class="abs pager" style="top:362px">
  <span style="border-color:#d0601c"><svg width="6" height="6" viewBox="0 0 6 6"><path d="M5 3H1M3 1L1 3l2 2" fill="none" stroke="#d0601c" stroke-width="1"/></svg></span>
  <span><svg width="6" height="6" viewBox="0 0 6 6"><path d="M1 3h4M3 1l2 2-2 2" fill="none" stroke="#999" stroke-width="1"/></svg></span>
</div>
<div class="abs card" style="left:81px;top:386px">
  <div class="overlay">
    <h4>Fusce magna magna gravida</h4>
    <p>Aliquam ornare, ligula quis molestie accumsan, dolor magna vestibulum mi, ut luctus risus nibh</p>
    <div class="price">$00.00</div>
  </div>
  <div class="actions">
    <svg role="img" aria-label="Buy" width="11" height="10" viewBox="0 0 10 10"><path d="M0 1h2l1.5 5h5L10 2.5H3" fill="none" stroke="#e0332f" stroke-width="1.4"/><circle cx="4" cy="8.5" r="1" fill="#e0332f"/><circle cx="8" cy="8.5" r="1" fill="#e0332f"/></svg>
    <svg role="img" aria-label="Rent" width="10" height="10" viewBox="0 0 10 10"><rect x="1" y="2" width="8" height="7" fill="none" stroke="#999"/><line x1="1" y1="4.3" x2="9" y2="4.3" stroke="#999"/><line x1="3" y1="1" x2="3" y2="3" stroke="#999"/><line x1="7" y1="1" x2="7" y2="3" stroke="#999"/></svg>
    <svg role="img" aria-label="Quick view" width="12" height="10" viewBox="0 0 12 8"><path d="M0.5 4C3 0 9 0 11.5 4 9 8 3 8 0.5 4z" fill="none" stroke="#999"/><circle cx="6" cy="4" r="1.8" fill="#999"/></svg>
  </div>
</div>
<div class="abs card" style="left:226px;top:386px"><div class="shot" role="img" aria-label="Times Square billboards at dusk" style="background:linear-gradient(160deg,#3a3f5c,#7b5468 50%,#2e2f3b)"></div><div class="caption">Fusce magna magna gravida</div></div>
<div class="abs card" style="left:371px;top:386px"><div class="shot" role="img" aria-label="City square with large LED screens" style="background:linear-gradient(180deg,#3d78c2,#a0584a 55%,#5b4a44)"></div><div class="caption">Fusce magna magna gravida</div></div>
<div class="abs card" style="left:516px;top:386px"><div class="shot" role="img" aria-label="Illuminated billboards at night" style="background:linear-gradient(180deg,#0e1320,#38405a 55%,#1a1c24)"></div><div class="caption">Fusce magna magna gravida</div></div>

<!-- Trusses -->
<h2 class="abs section-title" style="top:554px;color:var(--accent-blue)">Trusses</h2>
<div class="abs pager" style="top:556px">
  <span style="border-color:#1d5aa8"><svg width="6" height="6" viewBox="0 0 6 6"><path d="M5 3H1M3 1L1 3l2 2" fill="none" stroke="#1d5aa8" stroke-width="1"/></svg></span>
  <span><svg width="6" height="6" viewBox="0 0 6 6"><path d="M1 3h4M3 1l2 2-2 2" fill="none" stroke="#999" stroke-width="1"/></svg></span>
</div>
<div class="abs card" style="left:81px;top:580px"><div class="shot" role="img" aria-label="Truss frame with lit white panel" style="background:linear-gradient(180deg,#1a1a1a,#9a9a9a 50%,#2a2a2a)"></div><div class="caption">Fusce magna magna gravida</div></div>
<div class="abs card" style="left:226px;top:580px"><div class="shot" role="img" aria-label="Stage truss with backlit panel" style="background:linear-gradient(180deg,#151515,#8c8c8c 50%,#4a3222)"></div><div class="caption">Fusce magna magna gravida</div></div>
<div class="abs card" style="left:371px;top:580px"><div class="shot" role="img" aria-label="Two lit truss panels in dark room" style="background:linear-gradient(180deg,#1b1b1b,#6d6d6d 50%,#2a2a2a)"></div><div class="caption">Fusce magna magna gravida</div></div>
<div class="abs card" style="left:516px;top:580px"><div class="shot" role="img" aria-label="Empty warehouse with roof truss" style="background:linear-gradient(180deg,#7d8e9a,#b7c4cc 60%,#d4dadd)"></div><div class="caption">Fusce magna magna gravida</div></div>

<!-- Gas Station lights -->
<h2 class="abs section-title" style="top:748px;color:var(--accent-green)">Gas Station lights</h2>
<div class="abs pager" style="top:750px">
  <span style="border-color:#3aa53a"><svg width="6" height="6" viewBox="0 0 6 6"><path d="M5 3H1M3 1L1 3l2 2" fill="none" stroke="#3aa53a" stroke-width="1"/></svg></span>
  <span><svg width="6" height="6" viewBox="0 0 6 6"><path d="M1 3h4M3 1l2 2-2 2" fill="none" stroke="#999" stroke-width="1"/></svg></span>
</div>
<div class="abs card" style="left:81px;top:774px"><div class="shot" role="img" aria-label="Gas station canopy lit at night" style="background:linear-gradient(180deg,#1e2c44,#b86a2c 45%,#3a3a3a)"></div><div class="caption">Fusce magna magna gravida</div></div>
<div class="abs card" style="left:226px;top:774px"><div class="shot" role="img" aria-label="Yellow fuel pumps under canopy lights" style="background:linear-gradient(180deg,#2a2d34,#c9b23a 50%,#4a4a4a)"></div><div class="caption">Fusce magna magna gravida</div></div>
<div class="abs card" style="left:371px;top:774px"><div class="shot" role="img" aria-label="Fuel station forecourt at dusk" style="background:linear-gradient(180deg,#22324f,#c9cfd6 45%,#5a5d62)"></div><div class="caption">Fusce magna magna gravida</div></div>
<div class="abs card" style="left:516px;top:774px"><div class="shot" role="img" aria-label="Station canopy with blue and red lights at night" style="background:linear-gradient(180deg,#0b0f1c,#2c4d9a 45%,#1c1f2a)"></div><div class="caption">Fusce magna magna gravida</div></div>

<!-- About -->
<section class="abs about">
  <h2>About Calder Vane LED</h2>
  <p>Nulla facilisi. Vestibulum vehicula, risus ac convallis efficitur, quam purus feugiat lectus, vel consequat purus nisi blandit diam. Aliquam id iaculis erat. Mauris convallis magna ut purus porttitor pellentesque. Nullam faucibus fringilla accumsan. Morbi vitae est eu risus consequat volutpat. Pellentesque eleifend, sapien vel rutrum tempus, ligula libero pellentesque quam, id finibus enim eros in nisl. Fusce magna magna, gravida nec sem sed, mollis convallis dolor. In dapibus nulla in mauris aliquet congue. Morbi dictum lobortis justo non suscipit. Nam suscipit dolor eget ipsum molestie, eget gravida dolor efficitur. Etiam ultricies velit vitae aliquam ullamcorper. Vivamus efficitur tristique magna a dapibus. Duis quis mi tortor. Praesent quis diam elit.</p>
</section>

<!-- Footer links -->
<footer class="abs footer">
  <div class="abs fcol" style="left:81px">LED Billboards<ul><li>Integer vitae ligula</li><li>Aenean ullamcorper</li><li>Fusce euismod</li><li>Sed ligula metus</li><li>Nam suscipit</li></ul></div>
  <div class="abs vline" style="left:173px"></div>
  <div class="abs fcol" style="left:203px">Trusses<ul><li>Integer vitae ligula</li><li>Aenean ullamcorper</li><li>Fusce euismod</li><li>Sed ligula metus</li><li>Nam suscipit</li></ul></div>
  <div class="abs vline" style="left:303px"></div>
  <div class="abs fcol" style="left:340px">Gas Station lights<ul><li>Integer vitae ligula</li><li>Aenean ullamcorper</li><li>Fusce euismod</li><li>Sed ligula metus</li><li>Nam suscipit</li></ul></div>
  <div class="abs vline" style="left:445px"></div>
  <div class="abs fcol" style="left:481px">Service &amp; Support<ul><li>Customer Care</li><li>FAQ</li><li>Fusce euismod</li><li>Sed ligula metus</li><li>Nam suscipit</li></ul></div>
  <div class="abs vline" style="left:578px"></div>
  <div class="abs fcol" style="left:612px">My Account<ul><li>My Cart</li><li>Checkout</li><li>My Wishlist</li><li>Register</li><li>Log in</li></ul></div>
</footer>

<div class="abs bottom">
  <div class="abs copy">Copyright © 2016 &nbsp;Calder Vane LED. &nbsp;All rights reserved.</div>
  <div class="abs pay" style="left:520px;background:#e08a2a"></div>
  <div class="abs pay" style="left:538px;background:#2a62b8"></div>
  <div class="abs pay" style="left:556px;background:#c8c8c8"></div>
  <div class="abs pay" style="left:574px;background:#3a8fd0"></div>
  <div class="abs social" style="left:596px;background:#3b5a9a"></div>
  <div class="abs social" style="left:616px;background:#2a9ad8"></div>
  <div class="abs social" style="left:636px;background:#1a78b4"></div>
</div>

</body>
</html>
```